Tamquist - digital sales and services + dropshipping shopify

Hello
I’m reaching out because I need help improving my current website setup. While I like the unique design, the desktop version feels empty and incomplete, and I’d like to enhance it to make it more engaging and effective.
**Here are the key areas I need assistance with:**
1. **Desktop Version Enhancements:**
- Add more content, visuals, and interactive elements to fill the empty spaces.
- Optimize the layout to ensure it looks engaging and consistent across devices.
2. **E-commerce Integration:**
- I need to integrate Shopify (or a similar service) for managing sales, product listings, and payments efficiently.
- Set up sales funnels and automation to streamline lead conversion and order processing.
3. **Business Focus Areas:**
- The website should reflect my business focus on sales, lead generation, AI integration, efficient business setup, middlemen services, and dropshipping.
- I want clear sections dedicated to explaining these services and showcasing how they add value.
The goal is to make the website look and feel complete, especially on desktop, and to support my business model effectively.
I will also need more logos, that builds on my original logo, for the different niches we will launch in the future.
Can you help me with these updates, and if so, could you provide an estimate on the timeline and cost?
Looking forward to working with you!
Best regards,
Gordon
https://pagenook.co/Tamquist-Shelfset/shop
Industry/Entity Type
Leadgen, ai integration, api, digital services sales, dropshipping
Coding
Coded - Design and coding required
Number of Pages Required
5+ page
Look and feel

```html
<!DOCTYPE html>
<html lang="en">
<head>
<meta charset="utf-8">
<title>Tamquist – Digital Sales &amp; Services</title>
<link href="https://fonts.googleapis.com/css2?family=Audiowide&family=Roboto:wght@400;500;700&display=swap" rel="stylesheet">
<style>
:root{
  --green:#4d9f27;
  --green-dark:#3c8a1f;
  --bg-hero:#2a2a2a;
  --bg-dark:#232323;
  --bg-services:#252525;
  --bg-shop:#2a2a2a;
  --bg-about:#313131;
  --bg-card:#2d2d2d;
  --text:#ffffff;
  --muted:#b4b4b4;
}
*{margin:0;padding:0;box-sizing:border-box}
html,body{width:1200px;height:4619px;overflow:hidden;background:var(--bg-dark);font-family:"Roboto",Arial,sans-serif;color:var(--text)}
.page{position:relative;width:1200px;height:4619px;overflow:hidden}
.abs{position:absolute}
.display{font-family:"Audiowide",sans-serif;text-transform:uppercase;letter-spacing:1px;font-weight:400}
.section-title{position:absolute;left:0;width:1200px;text-align:center;font-size:40px}

/* top bar */
.topbar{left:0;top:0;width:1200px;height:29px;background:var(--green-dark);font-size:11px;font-weight:700}
.topbar .social{left:111px;top:9px;display:flex;gap:9px}
.topbar .social span{width:11px;height:11px;border-radius:50%;background:#fff;display:block}
.topbar .promo{left:0;width:1200px;top:8px;text-align:center}
.topbar .arrow{top:5px;font-size:14px}
.topbar .lang{left:902px;top:8px}
.topbar .region{left:978px;top:8px}

/* header */
.logo{left:111px;top:62px;display:flex;align-items:center;gap:10px;font-size:22px;font-weight:700;letter-spacing:2px}
.logo i{width:18px;height:18px;background:var(--green);display:block}
.nav{left:340px;top:56px;display:flex;gap:19px;font-size:13px}
.nav a{color:#fff;text-decoration:none}
.nav a.active{color:var(--green)}
.header-icons{left:998px;top:56px;display:flex;gap:16px}

/* hero */
.hero{left:0;top:0;width:1200px;height:720px;background:radial-gradient(circle at 75% 40%,#353535 0%,var(--bg-hero) 55%,#222 100%)}
.hero h1{left:111px;top:200px;font-size:40px;line-height:52px}
.btn{display:inline-block;background:var(--green);color:#fff;font-weight:700;font-size:15px;text-transform:uppercase;text-align:center}
.hero .btn{left:111px;top:441px;width:171px;height:52px;line-height:52px}
.hero-visual{left:628px;top:170px;width:475px;height:359px;border-radius:10px;background:linear-gradient(160deg,#1c1c1c 0%,#3a3f5a 55%,#121212 100%)}

/* services */
.services{left:0;top:720px;width:1200px;height:527px;background:var(--bg-services)}
.svc{position:absolute;width:205px}
.svc h3{font-size:16px;font-weight:700;text-transform:uppercase;margin-bottom:8px}
.svc p{font-size:13px;line-height:21px;color:var(--muted)}
.svc.left{left:110px;text-align:right}
.svc.right{left:885px;width:225px}
.svc-icon{position:absolute;width:56px;height:56px;border-radius:50%;background:#333;display:flex;align-items:center;justify-content:center}
.svc-icon.on{background:var(--green)}
.brand-mark{left:452px;top:140px;width:300px;height:270px;display:flex;align-items:center;justify-content:center;flex-direction:column;gap:18px}
.brand-mark i{width:120px;height:120px;border-radius:50%;background:var(--green);display:block}
.brand-mark span{font-size:26px;font-weight:700;letter-spacing:3px}

/* shop categories */
.shop{left:0;top:1247px;width:1200px;height:560px;background:var(--bg-shop)}
.cat{position:absolute;top:134px;width:259px}
.cat .img{height:306px;border-radius:6px}
.cat p{text-align:center;font-weight:700;font-size:16px;margin-top:28px}

/* about */
.about{left:0;top:1790px;width:1200px;height:820px;background:radial-gradient(circle at 30% 50%,#3a3a3a 0%,var(--bg-about) 60%)}
.about .mark{left:140px;top:220px;width:380px;height:380px;display:flex;flex-direction:column;align-items:center;justify-content:center;gap:20px}
.about .mark i{width:200px;height:200px;border-radius:50%;background:linear-gradient(160deg,#6dc23a,var(--green-dark));display:block}
.about .mark span{font-size:28px;font-weight:700;letter-spacing:3px}
.about h2{left:651px;top:218px;font-size:38px}
.about .copy{left:651px;top:290px;width:438px;font-size:13.5px;line-height:25px;color:#e6e6e6;text-align:justify}
.about .copy p+p{margin-top:16px}
.about .btn{left:651px;top:542px;width:151px;height:49px;line-height:49px;font-size:14px}

/* new arrivals */
.arrivals{left:0;top:2610px;width:1200px;height:605px;background:#262626}
.card{position:absolute;top:138px;width:230px;height:361px;background:var(--bg-card);border:1px solid #3a3a3a;border-radius:6px;text-align:center}
.card.hover{border:2px solid var(--green)}
.card .img{height:216px;border-radius:5px 5px 0 0;position:relative}
.card .badge{position:absolute;left:10px;top:10px;background:var(--green);font-size:9px;font-weight:700;padding:3px 5px;border-radius:2px}
.card h4{font-size:15px;font-weight:500;text-transform:uppercase;margin-top:30px;letter-spacing:.5px}
.card .price{margin-top:12px;font-size:14px}
.card .price s{color:#888;font-size:12px;margin-right:8px}
.card .price b{color:var(--green);font-size:17px}
.card .cart{position:absolute;left:10px;right:10px;bottom:10px;height:32px;line-height:32px;background:#222;font-weight:700;font-size:14px}
.card.hover .cart{background:var(--green)}

/* values */
.values{left:0;top:3215px;width:1200px;height:567px;background:var(--bg-dark)}
.values h2{left:111px;top:56px;font-size:38px}
.value{position:absolute;left:111px;width:440px}
.value .ic{position:absolute;left:0;top:0;width:60px;height:60px;border-radius:50%;background:var(--green);display:flex;align-items:center;justify-content:center}
.value h3{margin-left:88px;font-size:18px;font-weight:700;text-transform:uppercase}
.value p{margin-left:88px;margin-top:8px;font-size:14px;line-height:22px;color:#e0e0e0}
.values .btn-light{left:111px;top:450px;width:181px;height:44px;line-height:44px;background:#fff;color:var(--green);font-weight:700;font-size:14px;text-align:center}
.values .photo{left:610px;top:0;width:590px;height:567px;background:linear-gradient(180deg,#6d6660 0%,#d8d1c6 55%,#b9b0a3 100%)}

/* newsletter */
.newsletter{left:0;top:3782px;width:1200px;height:500px;background:#222}
.newsletter h2{top:82px}
.newsletter .sub{left:0;width:1200px;top:140px;text-align:center;font-size:14px}
.field{position:absolute;top:204px;width:391px;height:45px;background:#fff;color:#999;font-size:14px;padding:14px 20px}
.newsletter .btn{left:518px;top:278px;width:162px;height:45px;line-height:45px;font-size:15px}

/* footer */
.footer{left:0;top:4282px;width:1200px;height:337px;background:#2a2a2a}
.fcol{position:absolute;top:55px}
.fcol h5{font-size:15px;font-weight:500;text-transform:uppercase;margin-bottom:16px}
.fcol li{list-style:none;font-size:12px;line-height:22.5px}
.follow li{display:flex;align-items:center;gap:12px;line-height:34px}
.follow i{width:26px;height:26px;border-radius:50%;background:var(--green);display:block}
.divider{position:absolute;top:60px;width:1px;height:150px;background:#3c3c3c}
.payments{left:516px;top:276px;display:flex;gap:5px}
.payments span{width:30px;height:18px;border-radius:3px;background:#3f63b8;display:block}
.copyright{left:0;width:1200px;top:308px;text-align:center;font-size:11px}
</style>
</head>
<body>
<div class="page">

  <!-- hero -->
  <section class="hero abs">
    <h1 class="abs display">Just a tiny click<br>away from<br>transforming<br>your everyday</h1>
    <a class="abs btn">Get Started</a>
    <div class="abs hero-visual" role="img" aria-label="Product photo: desk monitor above a keyboard shortcut desk mat"></div>
    <svg class="abs" style="left:0;top:0" width="1200" height="720" viewBox="0 0 1200 720">
      <polygon points="0,555 600,690 1200,565 1200,592 600,716 0,582" fill="var(--green)"/>
      <polygon points="0,582 600,716 1200,592 1200,720 0,720" fill="var(--bg-services)"/>
    </svg>
  </section>

  <!-- top bar -->
  <div class="abs topbar">
    <div class="abs social"><span></span><span></span><span></span><span></span></div>
    <div class="abs promo">FREE SHIPPING FOR ALL ORDER OF $99</div>
    <div class="abs arrow" style="left:369px">&#8249;</div>
    <div class="abs arrow" style="left:823px">&#8250;</div>
    <div class="abs lang">English &#8964;</div>
    <div class="abs region">United States ( $ ) &#8964;</div>
  </div>

  <!-- header -->
  <div class="abs logo"><i></i>TAMQUIST</div>
  <nav class="abs nav">
    <a class="active">Home</a><a>About Us</a><a>Services</a><a>Categories</a><a>Shop</a><a>Top 17 AI tools for business!</a>
  </nav>
  <div class="abs header-icons">
    <svg width="16" height="16" viewBox="0 0 16 16" fill="none" stroke="#fff" stroke-width="1.6"><circle cx="7" cy="7" r="5"/><line x1="11" y1="11" x2="15" y2="15"/></svg>
    <svg width="16" height="16" viewBox="0 0 16 16" fill="none" stroke="#fff" stroke-width="1.6"><circle cx="8" cy="5" r="3.5"/><path d="M2 15c0-3.5 2.7-5.5 6-5.5s6 2 6 5.5"/></svg>
    <svg width="18" height="16" viewBox="0 0 18 16" fill="none" stroke="#fff" stroke-width="1.6"><path d="M1 2h3l2 9h9l2-7H5"/><circle cx="7" cy="14" r="1"/><circle cx="14" cy="14" r="1"/></svg>
  </div>

  <!-- services -->
  <section class="abs services">
    <h2 class="section-title display" style="top:44px">Our Services</h2>

    <div class="svc left" style="top:128px"><h3>Sales</h3><p>Lorem ipsum dolor sit amet, consectetur adipiscing elit, sed do eiusmod tempor</p></div>
    <div class="svc left" style="top:246px"><h3>Lead Generation</h3><p>Lorem ipsum dolor sit amet, consectetur adipiscing elit, sed do eiusmod tempor</p></div>
    <div class="svc left" style="top:364px"><h3>AI Integration</h3><p>Lorem ipsum dolor sit amet, consectetur adipiscing elit, sed do eiusmod tempor</p></div>

    <div class="svc-icon" style="left:342px;top:133px"><svg width="26" height="26" viewBox="0 0 26 26" fill="none" stroke="var(--green)" stroke-width="1.6"><circle cx="13" cy="13" r="10"/><path d="M13 7v12M9 10h6a2 2 0 010 4h-4a2 2 0 000 4h6"/></svg></div>
    <div class="svc-icon on" style="left:342px;top:251px"><svg width="26" height="26" viewBox="0 0 26 26" fill="none" stroke="#fff" stroke-width="1.6"><path d="M3 5h20l-8 9v7l-4 2v-9z"/></svg></div>
    <div class="svc-icon" style="left:342px;top:369px"><svg width="26" height="26" viewBox="0 0 26 26" fill="none" stroke="var(--green)" stroke-width="1.6"><rect x="7" y="7" width="12" height="12" rx="2"/><path d="M10 3v4M16 3v4M10 19v4M16 19v4M3 10h4M3 16h4M19 10h4M19 16h4"/></svg></div>

    <div class="abs brand-mark" role="img" aria-label="Tamquist brand mark"><i></i><span>TAMQUIST</span></div>

    <div class="svc-icon" style="left:804px;top:133px"><svg width="26" height="26" viewBox="0 0 26 26" fill="none" stroke="var(--green)" stroke-width="1.6"><circle cx="13" cy="13" r="10"/><circle cx="13" cy="13" r="4"/><path d="M13 3v4M13 19v4M3 13h4M19 13h4"/></svg></div>
    <div class="svc-icon" style="left:804px;top:251px"><svg width="26" height="26" viewBox="0 0 26 26" fill="none" stroke="var(--green)" stroke-width="1.6"><circle cx="13" cy="6" r="3"/><circle cx="5" cy="18" r="3"/><circle cx="21" cy="18" r="3"/><path d="M13 9v5M13 14l-6 2M13 14l6 2"/></svg></div>
    <div class="svc-icon" style="left:804px;top:369px"><svg width="26" height="26" viewBox="0 0 26 26" fill="none" stroke="var(--green)" stroke-width="1.6"><rect x="5" y="10" width="16" height="12" rx="1"/><path d="M9 10V7a4 4 0 018 0v3"/></svg></div>

    <div class="svc right" style="top:128px"><h3>Efficient Business Setup</h3><p>Lorem ipsum dolor sit amet, consectetur adipiscing elit, sed do eiusmod tempor</p></div>
    <div class="svc right" style="top:246px"><h3>Middlemen Services</h3><p>Lorem ipsum dolor sit amet, consectetur adipiscing elit, sed do eiusmod tempor</p></div>
    <div class="svc right" style="top:364px"><h3>Dropshipping</h3><p>Lorem ipsum dolor sit amet, consectetur adipiscing elit, sed do eiusmod tempor</p></div>
  </section>

  <!-- shop categories -->
  <section class="abs shop">
    <h2 class="section-title display" style="top:50px">Shop Categories</h2>
    <div class="cat" style="left:111px"><div class="img" role="img" aria-label="Hacker sheet desk mat with keyboard and monitor" style="background:linear-gradient(180deg,#f2f2f2 0%,#e7e7e7 30%,#2a2a2a 45%,#3b2230 65%,#ececec 80%)"></div><p>Hacker Sheet</p></div>
    <div class="cat" style="left:396px"><div class="img" role="img" aria-label="Modern office desk with chairs" style="background:linear-gradient(180deg,#d9d6d1 0%,#a9a49d 55%,#cbc7c1 100%)"></div><p>Office Furniture</p></div>
    <div class="cat" style="left:682px"><div class="img" role="img" aria-label="Office dashboard modules on screen" style="background:linear-gradient(180deg,#3c2a8a 0%,#121226 35%,#0e1a1d 100%)"></div><p>Office Modules</p></div>
    <div class="cat" style="left:967px"><div class="img" role="img" aria-label="Leather passport travel cases" style="background:linear-gradient(90deg,#2f3c56 0%,#6b2a2a 30%,#8a6248 60%,#b99b7e 100%)"></div><p>Travel Case</p></div>
  </section>

  <!-- about -->
  <section class="abs about">
    <svg class="abs" style="left:0;top:0" width="1200" height="820" viewBox="0 0 1200 820">
      <polygon points="0,0 1200,0 1200,138 377,4 0,138" fill="var(--bg-shop)"/>
      <polygon points="0,138 377,4 1200,138 1200,158 377,26 0,158" fill="var(--green)"/>
      <polygon points="0,642 829,777 1200,652 1200,672 829,798 0,662" fill="var(--green)"/>
      <polygon points="0,662 829,798 1200,672 1200,820 0,820" fill="#262626"/>
    </svg>
    <div class="abs mark" role="img" aria-label="Tamquist brand mark"><i></i><span>TAMQUIST</span></div>
    <h2 class="abs display">About Us</h2>
    <div class="abs copy">
      <p>At Tamquist, we value community and community building around hobbies and interests. We want to create more than just a store – we want to build a network of people who share a passion for quality and good experiences.</p>
      <p>Our business model focuses on carefully selected, high quality products. We specialize in these products to avoid competing on price with everyone else, and instead offer a genuine experience and an active community for our customers.</p>
    </div>
    <a class="abs btn">Learn More</a>
  </section>

  <!-- new arrivals -->
  <section class="abs arrivals">
    <h2 class="section-title display" style="top:52px">New Arrival Products</h2>
    <div class="card" style="left:111px"><div class="img" role="img" aria-label="Shortcut desk mat with keyboard" style="background:linear-gradient(180deg,#e9e9e9 0%,#cfcfcf 35%,#1b1b1b 55%,#2b2b2b 100%)"><span class="badge">25% off</span></div><h4>Product Name 1</h4><div class="price"><s>$25.00</s><b>$18.75</b></div><div class="cart">Add To Cart</div></div>
    <div class="card" style="left:361px"><div class="img" role="img" aria-label="Glass top office desk with drawers" style="background:linear-gradient(180deg,#dad8d4 0%,#8d8a85 55%,#c9c6c1 100%)"><span class="badge">25% off</span></div><h4>Product Name 1</h4><div class="price"><s>$25.00</s><b>$18.75</b></div><div class="cart">Add To Cart</div></div>
    <div class="card hover" style="left:610px"><div class="img" role="img" aria-label="Office module dashboard screens" style="background:linear-gradient(180deg,#1f3b36 0%,#0d0d12 40%,#28203a 100%)"><span class="badge">25% off</span></div><h4>Product Name 1</h4><div class="price"><s>$25.00</s><b>$18.75</b></div><div class="cart">Add To Cart</div></div>
    <div class="card" style="left:858px"><div class="img" role="img" aria-label="Printed cheat sheet with pen" style="background:linear-gradient(90deg,#f3f3f3 0%,#e8e8e8 30%,#1c1c1c 45%,#2a2a2a 85%,#f0f0f0 100%)"><span class="badge">25% off</span></div><h4>Product Name 1</h4><div class="price"><s>$25.00</s><b>$18.75</b></div><div class="cart">Add To Cart</div></div>
  </section>

  <!-- values -->
  <section class="abs values">
    <h2 class="abs display">Our Values</h2>
    <div class="value" style="top:136px"><div class="ic"><svg width="28" height="28" viewBox="0 0 28 28" fill="none" stroke="#fff" stroke-width="1.8"><rect x="4" y="16" width="5" height="8"/><rect x="11.5" y="11" width="5" height="13"/><rect x="19" y="6" width="5" height="18"/></svg></div><h3>Executives</h3><p>Lorem ipsum dolor sit amet, consectetur adipiscing elit, sed do eiusmod tempor incididunt</p></div>
    <div class="value" style="top:237px"><div class="ic"><svg width="28" height="28" viewBox="0 0 28 28" fill="none" stroke="#fff" stroke-width="1.8"><circle cx="14" cy="14" r="10"/><path d="M14 8v12M10.5 11h5a2 2 0 010 4h-3a2 2 0 000 4h5"/></svg></div><h3>Investors</h3><p>Lorem ipsum dolor sit amet, consectetur adipiscing elit, sed do eiusmod tempor incididunt</p></div>
    <div class="value" style="top:338px"><div class="ic"><svg width="28" height="28" viewBox="0 0 28 28" fill="none" stroke="#fff" stroke-width="1.8"><path d="M4 20l7-7 5 5 8-9"/><path d="M18 9h6v6"/></svg></div><h3>Entrepreneurs</h3><p>Lorem ipsum dolor sit amet, consectetur adipiscing elit, sed do eiusmod tempor incididunt</p></div>
    <a class="abs btn-light">LEARN MORE &#10140;</a>
    <div class="abs photo" role="img" aria-label="Bright executive office interior with desk, chair and shelving"></div>
  </section>

  <!-- newsletter -->
  <section class="abs newsletter">
    <h2 class="section-title display">Newsletter Signup</h2>
    <p class="abs sub">Subscribe to our mailing list for all our latest offers and ideas.</p>
    <div class="field" style="left:194px">Your Name</div>
    <div class="field" style="left:615px">Email Address</div>
    <a class="abs btn">Subscribe</a>
    <svg class="abs" style="left:0;top:385px" width="1200" height="115" viewBox="0 0 1200 115">
      <polygon points="0,112 600,19 1200,112 1200,115 0,115" fill="#2a2a2a"/>
      <polygon points="0,82 600,0 1200,82 1200,112 600,19 0,112" fill="var(--green)"/>
    </svg>
  </section>

  <!-- footer -->
  <footer class="abs footer">
    <div class="fcol" style="left:113px"><h5>Quick Links</h5><ul><li>Home</li><li>About Us</li><li>Services</li><li>Categories</li><li>Shop</li><li>Top 17 AI tools for business!</li></ul></div>
    <div class="divider" style="left:270px"></div>
    <div class="fcol" style="left:350px"><h5>Information</h5><ul><li>Terms &amp; Conditions</li><li>Privacy Policy</li><li>Disclaimer</li><li>Site Map</li><li>Contact Us</li><li>Categories</li></ul></div>
    <div class="divider" style="left:535px"></div>
    <div class="fcol" style="left:615px;width:180px"><h5>Contact Info</h5><ul><li>(555) 014-7720</li><li style="margin-top:8px">(555) 014-7720</li><li style="margin-top:8px;text-decoration:underline">info@tamquist-shop.co</li><li style="margin-top:8px;line-height:15px">#2868 Lorem ipsum dolor sit amet, consectetur</li></ul></div>
    <div class="divider" style="left:875px"></div>
    <div class="fcol follow" style="left:953px"><h5>Follow Us</h5><ul><li><i></i>Friendnet</li><li><i></i>Chirpline</li><li><i></i>Circle Plus</li><li><i></i>Linkpro</li></ul></div>
    <div class="abs payments"><span></span><span></span><span></span><span></span><span></span></div>
    <div class="abs copyright">Copyrights © The Company name 2024 | Allrights Reserved</div>
  </footer>

</div>
</body>
</html>
```